Business card for medical clinic

I need an upmarket, modern medical/health business card for my clinic

Contact Information for Business Card

name, address, email, qr code

```html
<!DOCTYPE html>
<html lang="en">
<head>
<meta charset="utf-8">
<title>Novara Care Partners – Business Card</title>
<link href="https://fonts.googleapis.com/css2?family=Poppins:wght@300;400;500;600&display=swap" rel="stylesheet">
<style>
  :root {
    --stage: #222222;
    --card: #1c1c1c;
    --blue: #1f9bd7;
    --blue-deep: #1578b0;
    --white: #f4f6f8;
    --sheen: #dfe9f1;
    --divider: #2f8fc4;
  }
  * { box-sizing: border-box; margin: 0; padding: 0; }
  html, body { width: 1200px; height: 711px; overflow: hidden; background: var(--stage); }
  body { font-family: "Poppins", sans-serif; position: relative; }

  .card {
    position: absolute;
    top: 205px;
    width: 525px;
    height: 300px;
    background: var(--card);
    border-radius: 18px;
    overflow: hidden;
    box-shadow: 0 14px 30px rgba(0,0,0,.55);
  }
  .card--front { left: 50px; }
  .card--back { left: 625px; }

  .card__band { position: absolute; left: 0; bottom: 0; width: 100%; height: 44px; }

  /* brand name (logo stand-in) */
  .brand { position: absolute; display: flex; align-items: center; }
  .brand__dot { border-radius: 50%; background: var(--blue); flex: none; }
  .brand__name { color: var(--blue); font-weight: 500; letter-spacing: .08em; text-transform: uppercase; line-height: 1.15; }

  .card--front .brand { left: 90px; top: 100px; gap: 18px; }
  .card--front .brand__dot { width: 54px; height: 54px; }
  .card--front .brand__name { font-size: 27px; }

  .card--back .brand { left: 32px; top: 122px; gap: 10px; }
  .card--back .brand__dot { width: 30px; height: 30px; }
  .card--back .brand__name { font-size: 15px; }

  .divider { position: absolute; left: 268px; top: 52px; width: 1px; height: 150px; background: linear-gradient(var(--card), var(--divider)); }

  .person { position: absolute; left: 292px; top: 48px; }
  .person__name { font-size: 30px; color: var(--blue); line-height: 1.1; }
  .person__first { font-weight: 600; }
  .person__last { font-weight: 300; }
  .person__role { font-size: 13px; color: var(--white); font-weight: 500; margin-top: 2px; }

  .contacts { position: absolute; left: 292px; top: 128px; list-style: none; }
  .contacts__item { display: flex; align-items: center; gap: 8px; color: var(--white); font-size: 13px; font-weight: 400; line-height: 22px; }
  .contacts__icon { width: 13px; height: 13px; flex: none; }

  .address { position: absolute; left: 0; right: 0; top: 222px; text-align: center; color: var(--blue); font-size: 14px; font-weight: 400; }
</style>
</head>
<body>

<section class="card card--front" aria-label="Card front">
  <div class="brand">
    <span class="brand__dot"></span>
    <span class="brand__name">Novara Care<br>Partners</span>
  </div>
  <svg class="card__band" viewBox="0 0 525 44" preserveAspectRatio="none" aria-hidden="true">
    <defs>
      <linearGradient id="bandFront" x1="0" y1="0" x2="0" y2="1">
        <stop offset="0" stop-color="var(--sheen)"/>
        <stop offset=".35" stop-color="var(--blue)"/>
        <stop offset="1" stop-color="var(--blue-deep)"/>
      </linearGradient>
    </defs>
    <polygon points="0,26 300,26 300,44 0,44" fill="url(#bandFront)"/>
    <polygon points="300,14 525,14 525,44 300,44" fill="url(#bandFront)"/>
    <polygon points="285,26 318,14 330,14 297,26" fill="var(--card)"/>
  </svg>
</section>

<section class="card card--back" aria-label="Card back">
  <div class="brand">
    <span class="brand__dot"></span>
    <span class="brand__name">Novara Care<br>Partners</span>
  </div>

  <div class="divider"></div>

  <div class="person">
    <p class="person__name"><span class="person__first">Marta</span> <span class="person__last">Lenova</span></p>
    <p class="person__role">Founder &amp; CEO</p>
  </div>

  <ul class="contacts">
    <li class="contacts__item">
      <svg class="contacts__icon" viewBox="0 0 16 16" aria-hidden="true"><path fill="var(--blue)" d="M3.6 1.2l2.3 2.6-1.2 1.8c.9 2 2.5 3.6 4.6 4.6l1.8-1.2 2.6 2.3-1.3 2.4C7.2 13.5 2.5 8.8 1.2 3z"/></svg>
      (555) 214-0387
    </li>
    <li class="contacts__item">
      <svg class="contacts__icon" viewBox="0 0 16 16" aria-hidden="true"><circle cx="8" cy="8" r="6.5" fill="none" stroke="var(--blue)" stroke-width="1.6"/><path d="M1.5 8h13M8 1.5c-3 3.5-3 9.5 0 13M8 1.5c3 3.5 3 9.5 0 13" fill="none" stroke="var(--blue)" stroke-width="1.2"/></svg>
      info@novaracare.com
    </li>
    <li class="contacts__item">
      <svg class="contacts__icon" viewBox="0 0 16 16" aria-hidden="true"><rect x="1" y="3" width="14" height="10" rx="1.5" fill="var(--blue)"/><path d="M1.5 4l6.5 5 6.5-5" fill="none" stroke="var(--card)" stroke-width="1.3"/></svg>
      www.novaracare.com
    </li>
  </ul>

  <p class="address">4180 Linden Ave. Suite 120 Riverton, TX 75012</p>

  <svg class="card__band" viewBox="0 0 525 44" preserveAspectRatio="none" aria-hidden="true">
    <defs>
      <linearGradient id="bandBack" x1="0" y1="0" x2="0" y2="1">
        <stop offset="0" stop-color="var(--sheen)"/>
        <stop offset=".35" stop-color="var(--blue)"/>
        <stop offset="1" stop-color="var(--blue-deep)"/>
      </linearGradient>
    </defs>
    <polygon points="0,26 300,26 300,44 0,44" fill="url(#bandBack)"/>
    <polygon points="300,14 525,14 525,44 300,44" fill="url(#bandBack)"/>
    <polygon points="285,26 318,14 330,14 297,26" fill="var(--card)"/>
  </svg>
</section>

</body>
</html>
```